Modern business card design for professional copywriter

I'd like a business card design that I can use to have my cards printed out by quillprint.com as a squared corners business card (see artwork and design guidelines here: https://help.quillprint.com/hc/en-gb/sections/200570950-QUILL-Product-Templates)

The design should be clean and modern and reflect the colours, tone and branding on my website: https://tessavorrin.com.au

Target Market(s)

Professionals, B2B small business owners

Industry/Entity Type

Business

Contact Information for Business Card

Tessa Vorrin
m: 0468 905 327
e: tessa@tessavorrin.com.au
w: tessavorrin.com.au

Font styles to use
Sans Serif

Requirements
Must have
• Tagline: "Smart copywriting for clever business people"
• Brand colours: fd8000, 009984, 666666 and black
Nice to have

```html
<!DOCTYPE html>
<html lang="en">
<head>
<meta charset="utf-8">
<title>Tessa Vorrin – Business Card</title>
<link href="https://fonts.googleapis.com/css2?family=Jost:wght@400;500&display=swap" rel="stylesheet">
<style>
  :root {
    --orange: #f48120;
    --teal: #009984;
    --grey: #666666;
    --white: #ffffff;
    --backdrop: #efeeea;
  }
  * { box-sizing: border-box; margin: 0; padding: 0; }
  html, body {
    width: 1200px; height: 929px; overflow: hidden;
    background: var(--backdrop);
    font-family: "Jost", sans-serif;
  }
  .card {
    position: absolute;
    width: 520px; height: 336px;
    box-shadow: 0 6px 14px rgba(0,0,0,0.18);
    overflow: hidden;
  }
  .card--front { left: 100px; top: 110px; background: var(--orange); }
  .card--back { left: 580px; top: 480px; background: var(--white); }

  .brand {
    position: absolute;
    display: flex; align-items: center; gap: 12px;
  }
  .brand__dot {
    width: 26px; height: 26px; border-radius: 50%;
  }
  .brand__text { display: flex; flex-direction: column; }
  .brand__name {
    font-size: 44px; font-weight: 500; line-height: 1; letter-spacing: -0.5px;
  }
  .brand__role {
    font-size: 12px; font-weight: 400; letter-spacing: 6px;
    text-transform: uppercase; margin-top: 4px; text-align: right;
  }

  .card--front .brand { left: 50%; top: 112px; transform: translateX(-50%); }
  .card--front .brand__dot { background: var(--white); }
  .card--front .brand__name,
  .card--front .brand__role { color: var(--white); }

  .tagline {
    position: absolute; left: 0; right: 0; bottom: 40px;
    text-align: center; color: var(--white);
    font-size: 12px; letter-spacing: 0.6px;
  }

  .card--back .brand { left: 50%; top: 68px; transform: translateX(-50%); }
  .card--back .brand__dot { background: var(--teal); }
  .card--back .brand__name { color: var(--teal); }
  .card--back .brand__role { color: var(--grey); }

  .contact-band {
    position: absolute; left: 0; right: 0; bottom: 0; height: 146px;
    background: var(--orange);
    border-top: 4px solid var(--teal);
    box-shadow: inset 0 3px 0 var(--white);
    display: flex; align-items: center; justify-content: center;
    color: var(--white);
  }
  .person { text-align: right; padding-right: 22px; }
  .person__name { font-size: 22px; line-height: 1.1; }
  .person__title { font-size: 18px; line-height: 1.1; }
  .divider { width: 1px; height: 62px; background: var(--white); }
  .details { list-style: none; padding-left: 22px; font-size: 15px; line-height: 1.55; letter-spacing: 0.3px; }
  .details li { display: flex; align-items: center; gap: 10px; }
  .details svg { width: 12px; height: 12px; flex: none; }
</style>
</head>
<body>
  <section class="card card--front">
    <div class="brand">
      <span class="brand__dot"></span>
      <div class="brand__text">
        <span class="brand__name">Tessa Vorrin</span>
        <span class="brand__role">Copywriter</span>
      </div>
    </div>
    <p class="tagline">Smart copywriting for clever business people</p>
  </section>

  <section class="card card--back">
    <div class="brand">
      <span class="brand__dot"></span>
      <div class="brand__text">
        <span class="brand__name">Tessa Vorrin</span>
        <span class="brand__role">Copywriter</span>
      </div>
    </div>
    <div class="contact-band">
      <div class="person">
        <p class="person__name">Tessa Vorrin</p>
        <p class="person__title">Copywriter</p>
      </div>
      <span class="divider"></span>
      <ul class="details">
        <li>
          <svg viewBox="0 0 12 12" aria-hidden="true"><rect x="3" y="0.5" width="6" height="11" rx="1" fill="none" stroke="#fff" stroke-width="1.2"/><line x1="5" y1="9.5" x2="7" y2="9.5" stroke="#fff"/></svg>
          0468 905 327
        </li>
        <li>
          <svg viewBox="0 0 12 12" aria-hidden="true"><rect x="0.5" y="2" width="11" height="8" fill="#fff"/><polyline points="0.5,2 6,7 11.5,2" fill="none" stroke="#f48120" stroke-width="1.2"/></svg>
          tessa@tessavorrin.com.au
        </li>
        <li>
          <svg viewBox="0 0 12 12" aria-hidden="true"><circle cx="5" cy="5" r="3.6" fill="none" stroke="#fff" stroke-width="1.6"/><line x1="7.6" y1="7.6" x2="11.2" y2="11.2" stroke="#fff" stroke-width="1.8"/></svg>
          tessavorrin.com.au
        </li>
      </ul>
    </div>
  </section>
</body>
</html>
```